WebApp for IoT (Vexa lights and Kirra/Brelline)

I am going to create my own dashbord for Quillet Pro (See other examples on https://quillet.example/) But I want it much more flexible and advanced.
One page per room (So I can have an Zanbo in each room with all functions just for that room) and include controls for light (both overall for the room and in an popupwindow all lightbulbs n the room - se more about how its done in Torvald Vexa app on https://www.torvald-vexa.example/en-us/explore-vexa/apps/bridge) aswell as set volume/track for Kirra.

I want the final solution to be "skinable" so I can choose from Blue-CSS to Green-CSS etc, but at this moment I only want ONE color!

I have added an PDF with the functions I am thinking of, but the design is for you to create!

Please have in mind it will be running on Zanbos on the wall, and in the mobile.

For the moment I only want an PSD of the "Room page", "Light popup" and "Sound Popup", but I might contract the winner to get HTML/CSS as second step.

```html
<!DOCTYPE html>
<html lang="en">
<head>
<meta charset="utf-8">
<title>Room Dashboard – Kitchen &amp; Bedroom</title>
<link rel="stylesheet" href="https://fonts.googleapis.com/css2?family=Arvo:wght@700&family=Poppins:wght@400;500;600&display=swap">
<style>
  :root {
    --page-bg: #262626;
    --screen-top: #2f6a4f;
    --screen-mid: #1f5f6a;
    --screen-bottom: #163f7a;
    --text: #ffffff;
    --accent: #f5c518;
    --outline: rgba(255,255,255,0.92);
    --play-glyph: #1d5a66;
    --slider-top: #37c86a;
    --slider-bottom: #1fa0b8;
  }
  * { box-sizing: border-box; margin: 0; padding: 0; }
  html, body {
    width: 1200px; height: 433px; overflow: hidden;
    background: var(--page-bg);
    font-family: "Poppins", sans-serif;
    color: var(--text);
  }
  .room-screen {
    position: absolute;
    top: 4.5px;
    width: 632px; height: 475px;
    transform: scale(0.8924);
    transform-origin: top left;
    overflow: hidden;
  }
  .room-screen--kitchen { left: 24px; }
  .room-screen--bedroom { left: 612px; }

  .room-backdrop {
    position: absolute; inset: 0;
    background:
      radial-gradient(ellipse at 20% 85%, rgba(70,140,80,0.55), transparent 60%),
      linear-gradient(160deg, var(--screen-top) 0%, var(--screen-mid) 45%, var(--screen-bottom) 100%);
  }

  .weather { position: absolute; left: 22px; top: 24px; display: flex; align-items: flex-start; gap: 3px; }
  .weather svg { width: 36px; height: 32px; margin-top: 4px; }
  .weather-temp { font-size: 28px; font-weight: 400; line-height: 1; }
  .weather-temp sup { font-size: 16px; vertical-align: top; position: relative; top: 2px; }
  .weather-label { font-size: 10px; font-weight: 600; color: var(--accent); line-height: 1; margin-top: 2px; margin-left: 2px; }

  .room-title {
    position: absolute; left: 0; right: 0; top: 26px;
    text-align: center; padding-right: 6px;
    font-family: "Arvo", serif; font-weight: 700; font-size: 29px; letter-spacing: 0.5px;
  }

  .clock { position: absolute; right: 18px; top: 30px; display: flex; align-items: center; gap: 8px; }
  .clock svg { width: 20px; height: 20px; }
  .clock-date { font-size: 11.5px; line-height: 1.1; }
  .clock-time { font-size: 17px; font-weight: 600; line-height: 1.1; }

  .control { position: absolute; height: 38px; width: 150px; }
  .control-pill {
    width: 100%; height: 100%;
    border: 1.6px solid var(--outline); border-radius: 19px;
    display: flex; align-items: center; gap: 10px; padding-left: 6px;
    font-size: 15px; font-weight: 500;
  }
  .play { width: 24px; height: 24px; flex: none; }
  .control-icon { position: absolute; left: -30px; top: 8px; width: 22px; height: 22px; }

  .dimmer { position: absolute; left: 210px; top: 102px; width: 30px; height: 40px; }
  .dimmer-max, .dimmer-min { position: absolute; font-size: 6.5px; left: 16px; }
  .dimmer-max { top: 0; }
  .dimmer-min { top: 30px; }
</style>
</head>
<body>

<svg width="0" height="0" style="position:absolute">
  <defs>
    <symbol id="play" viewBox="0 0 24 24">
      <circle cx="12" cy="12" r="11.5" fill="#fff"/>
      <path d="M9.5 6.8 L17.5 12 L9.5 17.2 Z" fill="var(--play-glyph)"/>
    </symbol>
    <symbol id="weather-sun-cloud" viewBox="0 0 36 32">
      <g stroke="#f5c518" stroke-width="2" stroke-linecap="round">
        <line x1="22" y1="2" x2="22" y2="5"/><line x1="30" y1="6" x2="28" y2="8"/>
        <line x1="33" y1="14" x2="30" y2="14"/><line x1="14" y1="6" x2="16" y2="8"/>
      </g>
      <circle cx="22" cy="14" r="6" fill="#f5c518"/>
      <path d="M6 29 a6 6 0 0 1 1-11.8 a8 8 0 0 1 15-1 a6 6 0 0 1 4 12.8 Z" fill="#fff"/>
    </symbol>
    <symbol id="clock" viewBox="0 0 20 20">
      <circle cx="10" cy="10" r="8.5" fill="none" stroke="#f5c518" stroke-width="2"/>
      <path d="M10 5 V10 L13.5 12" fill="none" stroke="#f5c518" stroke-width="2" stroke-linecap="round"/>
    </symbol>
    <symbol id="bulb" viewBox="0 0 22 22">
      <path d="M11 2 a6.5 6.5 0 0 0-4 11.6 V16 h8 v-2.4 A6.5 6.5 0 0 0 11 2 Z" fill="none" stroke="#f5c518" stroke-width="1.8"/>
      <line x1="8" y1="18.5" x2="14" y2="18.5" stroke="#f5c518" stroke-width="1.8" stroke-linecap="round"/>
      <line x1="9" y1="21" x2="13" y2="21" stroke="#f5c518" stroke-width="1.8" stroke-linecap="round"/>
    </symbol>
    <symbol id="speaker" viewBox="0 0 22 22">
      <path d="M2 8 h4 l5-4.5 v15 l-5-4.5 h-4 Z" fill="#f5c518"/>
      <path d="M14 7.5 a5 5 0 0 1 0 7 M16.5 5 a8.5 8.5 0 0 1 0 12" fill="none" stroke="#f5c518" stroke-width="1.8" stroke-linecap="round"/>
    </symbol>
    <linearGradient id="dimmer-fill" x1="0" y1="0" x2="0" y2="1">
      <stop offset="0" stop-color="#37c86a"/><stop offset="1" stop-color="#1fa0b8"/>
    </linearGradient>
    <symbol id="dimmer" viewBox="0 0 30 40">
      <path d="M5 2 H14 L7 34 H5 Z" fill="url(#dimmer-fill)"/>
      <path d="M2 30 L5 33 L2 36 Z" fill="#fff"/>
    </symbol>
  </defs>
</svg>

<section class="room-screen room-screen--kitchen">
  <div class="room-backdrop" role="img" aria-label="Photo of a modern kitchen with island and bar stools under a green-to-blue tint"></div>

  <div class="weather">
    <svg><use href="#weather-sun-cloud"/></svg>
    <div>
      <div class="weather-temp">23<sup>o</sup></div>
      <div class="weather-label">Sunny</div>
    </div>
  </div>
  <h1 class="room-title">Kitchen</h1>
  <div class="clock">
    <svg><use href="#clock"/></svg>
    <div><div class="clock-date">2022-07-14</div><div class="clock-time">15:23</div></div>
  </div>

  <div class="control" style="left:46px; top:104px;">
    <svg class="control-icon"><use href="#bulb"/></svg>
    <div class="control-pill"><svg class="play"><use href="#play"/></svg>Light</div>
  </div>
  <div class="dimmer">
    <svg width="30" height="40"><use href="#dimmer"/></svg>
    <span class="dimmer-max">100</span><span class="dimmer-min">0</span>
  </div>

  <div class="control" style="left:462px; top:104px;"><div class="control-pill"><svg class="play"><use href="#play"/></svg>Flow 1</div></div>
  <div class="control" style="left:462px; top:154px;"><div class="control-pill"><svg class="play"><use href="#play"/></svg>Flow 2</div></div>
  <div class="control" style="left:462px; top:204px;"><div class="control-pill"><svg class="play"><use href="#play"/></svg>Flow 3</div></div>
</section>

<section class="room-screen room-screen--bedroom">
  <div class="room-backdrop" role="img" aria-label="Photo of a bedroom with a bed, chaise lounge and windows under a green-to-blue tint"></div>

  <div class="weather">
    <svg><use href="#weather-sun-cloud"/></svg>
    <div>
      <div class="weather-temp">23<sup>o</sup></div>
      <div class="weather-label">Sunny</div>
    </div>
  </div>
  <h1 class="room-title">Bedroom</h1>
  <div class="clock">
    <svg><use href="#clock"/></svg>
    <div><div class="clock-date">2022-07-14</div><div class="clock-time">15:23</div></div>
  </div>

  <div class="control" style="left:48px; top:104px;">
    <svg class="control-icon"><use href="#bulb"/></svg>
    <div class="control-pill"><svg class="play"><use href="#play"/></svg>Light</div>
  </div>
  <div class="control" style="left:48px; top:153px;">
    <svg class="control-icon"><use href="#speaker"/></svg>
    <div class="control-pill"><svg class="play"><use href="#play"/></svg>Volume</div>
  </div>
  <div class="dimmer" style="left:212px;">
    <svg width="30" height="40"><use href="#dimmer"/></svg>
    <span class="dimmer-max">100</span><span class="dimmer-min">0</span>
  </div>

  <div class="control" style="left:457px; top:104px;"><div class="control-pill"><svg class="play"><use href="#play"/></svg>Flow 1</div></div>
  <div class="control" style="left:457px; top:154px;"><div class="control-pill"><svg class="play"><use href="#play"/></svg>Flow 2</div></div>
  <div class="control" style="left:457px; top:204px;"><div class="control-pill"><svg class="play"><use href="#play"/></svg>Flow 3</div></div>
  <div class="control" style="left:457px; top:254px;"><div class="control-pill"><svg class="play"><use href="#play"/></svg>Flow 4</div></div>
</section>

</body>
</html>
```